Yoga/movement guide/teacher for adult yoga practice and kid yoga

What is the positioning or mission statement of your company? to guide individuals in a yoga-based safe and sustainable movement practice applicable to all ages and body types. Currently my focus is working with children in daycare and school settings, but my goal is to expand into private yoga practice for adults, and potentially as part of rented space in studios. I hope to find a way to work with children AND adults (so would love for logo to be appealing to both), but current focus is with children based on need and demand in the community. yoga for children also compliments my backround as a pediatrician/neonatologist, and I greatly miss interacting with children. I also want to emphasize a yoga/movement practice that is focused more on what one feels internally through movement. NOT what one looks like asthetically. I believe in removing all mirrors from yoga/movement practice. It should be an experience of movement/poses/yoga through appropriate cueing and education. It is not about the details of how far the knee should bend, or how high the leg should be. Focusing on foudation first, core, then core engagement and ultimately expression of poses/movements. A focus on strength, stability and mobility, not just flexibility, which is the common perception/association with yoga. I also want individuals to learn to be an advocate of their own health. Through guidance, I hope for individuals to connect with their body so they know themselves so well to be able to advocate for themselves in the modern healthcare world. This internal experience and connection is so essential in a world where modern medicine has become a business and it is all about making a dollar. the connection with patients is lost, and individuals need to learn to empower themselves and through their new found voice to be able to articulate what is wrong.<br/>Does your company have a tagline or slogan that should be included with the logo? "Move With Inner Light"<br/>What do you hope your company can be known for? Accessible yoga for a sustained practice. A guided movement practice where one gains information and knowledge of oneself through a mind/body connection. For one feel good physically with a new awaraness of their internal radiance that exists in all beings. Physical rejuvenation egnites a light and increases energy to flow through the physical body, which ultimately tranlates into works of kindness for others and out in the world. <br/>What color palettes might you prefer? why? love the colors currently chosen<br/>Where will the logo be primarily used? initially business cards, but hopefully future websites, t-shirts, and potentially local magazine adds. Also starting with a small couple of banners for community events in the area. I currently practice as a nomad out of my car :)<br/>Are there any elements you would prefer to see in the logo? Movement. A modern depiction of a human body/figure practicing movement. Hoping to avoid a stereotypical yoga pose per say, just because I want to people to think of it more of a movement practice with yoga roots. Modern yoga. There are elements of breathing and connecting with oneself through the flow of breath and movement, but I do not focus on the meditative/cerebral aspect of the yoga practice. What I teach is almost reaching a meditative state through movement. I personally don't practice, nor resonate with just seated meditation. just not my thing :)<br/>In your opinion, what defines a well-designed logo? curiosity. enough info for individuals to think they know what it means, but want to know more. invokes curiosity, but not too abstract. Reproducible. not too complicated. I want also to invoke a community feel, so a design that appeals to all people within a community. <br/>What is your preference in reference to icons, typography, spokespeople (characters), etc.? modern design. I love the idea of a logo for my purposes, to invoke a sense of movement from within. So not too static. <br/>What words or icons must be included in the logo? movement with yoga roots. <br/>What logos do you like and why? A representation, but not exact. I think some ambiguity is intriguing for others, and also memorable. I want it to be an artistic representation of movement/yoga<br/>What logos do you dislike and why? too busy, too loud. <br/>In your opinion, what is the primary purpose for a logo? association<br/>Who is the primary target audience? (who is most likely to use your services/product?) Children and their parents, but ultimately to expand into teaching adults. I even have aspirations of prenatal and post-natal yoga. Potentially incorporating infants. <br/>Who currently uses your product the most? n/a (working in schools/daycare currently. It is currently all volunteer)<br/>Are you pleased with the range of people your company serves? n/a<br/>Are you looking to expand, modify, or completely change your target audience? or will it remain the same? yes! expand into an adult audience. <br/>How do you plan to focus on your target audience? currently by working through schools and daycares. hopefully ultimately through after school care programs and then offering kid yoga in an existing yoga studio (working on this with Q Studio in Ridgeland, currently)<br/>What are your main forms of advertising? word of mouth, schools, daycares. Happy kids talking to their parents about the yoga class they took and happy teachers :)<br/>How do most customers find out about your company?<br/>Which gender are you targeting? All genders! However, with kid yoga, often the maternal individual in the child's life is more involved with decision making as far as extracurricular activities

Target Market(s)

individuals and families interested in wellness and feeling great

Contact Information for Business Card

Dana Whitford
Yoga Instructor
RYT-200, RCYT

certified yoga teacher for adults and children

Colors

Designer to choose colors to be used in the design.

Requirements
Must have
• "Move With Inner Light"
Nice to have
• logo with same colors

```html
<!DOCTYPE html>
<html lang="en">
<head>
<meta charset="utf-8">
<title>Brightway Studio business card</title>
<link rel="stylesheet" href="https://fonts.googleapis.com/css2?family=Arimo:wght@400&family=Short+Stack&display=swap">
<style>
  :root {
    --stage: #2b2b2b;
    --card-white: #ffffff;
    --slate: #7b7c7b;
    --slate-deep: #757675;
    --sun: #f5d83a;
    --teal: #5fc8d0;
    --ink: #6f6f6f;
    --light: #ffffff;
  }
  * { margin: 0; padding: 0; box-sizing: border-box; }
  html, body { width: 1200px; height: 900px; overflow: hidden; background: var(--stage); }
  .canvas { position: relative; width: 1200px; height: 900px; }

  .card {
    position: absolute; left: 250px; width: 700px; height: 400px;
    overflow: hidden; box-shadow: 0 10px 30px rgba(0,0,0,.45);
  }
  .card--back { top: 40px; background: var(--slate); }
  .card--front { top: 470px; background: var(--card-white); }

  .back-texture { position: absolute; inset: 0; background: var(--slate); }

  .brand {
    position: absolute; display: flex; align-items: center; gap: 12px;
    font-family: "Arimo", sans-serif; font-weight: 400;
  }
  .brand__dot { width: 22px; height: 22px; border-radius: 50%; background: var(--sun); flex: none; }
  .card--back .brand { left: 0; right: 0; top: 178px; justify-content: center; }
  .card--back .brand__name { color: var(--sun); font-size: 36px; letter-spacing: 1px; }
  .card--front .brand { left: 56px; top: 110px; }
  .card--front .brand__name { color: var(--ink); font-size: 32px; letter-spacing: .5px; }

  .tagline {
    position: absolute; left: 92px; top: 158px;
    font-family: "Arimo", sans-serif; font-size: 11px; letter-spacing: 2px;
    text-transform: uppercase; color: var(--teal);
  }

  .wave { position: absolute; inset: 0; width: 700px; height: 400px; }

  .contact {
    position: absolute; right: 40px; top: 244px; text-align: right;
    font-family: "Arimo", sans-serif; color: var(--light);
  }
  .contact__name { font-family: "Short Stack", cursive; color: var(--sun); font-size: 30px; line-height: 1.1; }
  .contact__role { font-size: 18px; margin-bottom: 10px; }
  .contact__list { list-style: none; font-size: 17px; line-height: 24px; }
  .contact__list li { display: flex; justify-content: flex-end; align-items: center; gap: 10px; }
  .contact__list svg { width: 17px; height: 17px; flex: none; }
</style>
</head>
<body>
<main class="canvas">

  <section class="card card--back" aria-label="Card back">
    <div class="back-texture" role="img" aria-label="Faint grey spiral pattern"></div>
    <div class="brand">
      <span class="brand__dot"></span>
      <span class="brand__name">Brightway Studio</span>
    </div>
  </section>

  <section class="card card--front" aria-label="Card front">
    <div class="brand">
      <span class="brand__dot"></span>
      <span class="brand__name">Brightway Studio</span>
    </div>
    <p class="tagline">Move With Inner Light</p>

    <svg class="wave" viewBox="0 0 700 400" aria-hidden="true">
      <path d="M0,300 C150,340 300,320 400,230 C470,165 580,130 700,122 L700,400 L0,400 Z" fill="var(--slate-deep)"/>
      <path d="M0,268 C150,308 300,288 400,208 C470,143 580,108 700,100" fill="none" stroke="var(--teal)" stroke-width="10"/>
      <path d="M0,288 C120,318 220,320 300,305" fill="none" stroke="var(--teal)" stroke-width="8"/>
    </svg>

    <div class="contact">
      <p class="contact__name">Dana Whitford</p>
      <p class="contact__role">Owner-Operator</p>
      <ul class="contact__list">
        <li>601-555-0142
          <svg viewBox="0 0 20 20" fill="none" stroke="var(--teal)" stroke-width="1.6"><circle cx="10" cy="10" r="8.5"/><path d="M7 6l1.6 2.2-1 1.2c.8 1.5 1.6 2.3 3 3l1.2-1L14 13l-1 1.5c-3.5-.5-6-3-6.6-6.5z"/></svg>
        </li>
        <li>dana@brightwaystudio.com
          <svg viewBox="0 0 20 20" fill="none" stroke="var(--teal)" stroke-width="1.6"><rect x="2" y="4.5" width="16" height="11"/><path d="M2 4.5l8 6 8-6"/></svg>
        </li>
        <li>www.brightwaystudio.com
          <svg viewBox="0 0 20 20" fill="none" stroke="var(--teal)" stroke-width="1.6"><circle cx="10" cy="10" r="8.5"/><ellipse cx="10" cy="10" rx="3.6" ry="8.5"/><path d="M1.5 10h17M3 6h14M3 14h14"/></svg>
        </li>
      </ul>
    </div>
  </section>

</main>
</body>
</html>
```